HAIR EXTENSIONS

We need a web design for a company base in Chicago called Tresses by Jolavie. We sale 100% human hair in Brazilian body wave deep wave straight or natural curl, Peruvian body wave straight or deep wave. Malaysian loose straight or body wave, in the chicago land.
We also ship hair to any city or country. We like to see design that use the colors pinks & grays, or would just like to see some design creative with colors thats inviting.

Also I'm using the quillmoss template, Home- banner contact us, about us, Features- product side/left sidebar, Shop- wish list /shopping cart/ tracking your order / checkout/ order received.
Porfolio-filterable 4column portfolio
Blog. Buy now

Industry/Entity Type

Hair

Number of Pages Required

4 page

Colors
aaaaaa
606060
dddddd
eea4c8
d3a5cc
b868aa
a6459a
ffc213
1b1b1b

Requirements
Must have
• I NEED THE DESIGNER TO DO THE 4 PAGE LIKE THIS.
• 1.HOME-PAGE BANNER CONTACT US SOME PRODUCT WITH SIDING IMAGES OF THE TOP PROUDCT
• 2.PRODUCT WITH SHOPPING CART- I WANT SIDING BARS FOR PRODUCT & SHOPPING CART WITH TRACKING YOUR ORDERS CHECK OUT & ORDER RECEIVED.
• 3.PORFOLIO PHOTO-I WANT A FEATURES FOR CUSTOMERS TO UPLOAN THERE PICTURE & BLOG ON THE PAGE
• 4.ABOUT US- TALK ABOUT ARE COMPAMY.
Nice to have
• hello designer
• I was working with a web developer for my site be for i came to craftnookly & they build a site for me that i liked, You all can view it at www.Tressesbyjolavie.info
• long story short never could get them to finish the project after they got paid!!
• I know, why paid before its finish bad decision. So know I'm here starting over with you all.
• here is a list of my competition site
• www.lockswellhub.com
• www.vanoraloft.com
• www.pellinoshop.com
• So just to give some insight, I'm looking for something like the one i had builded.

```html
<!DOCTYPE html>
<html lang="en">
<head>
<meta charset="utf-8">
<title>Tresses by Jolavie — Hair Extensions</title>
<link href="https://fonts.googleapis.com/css2?family=Nunito+Sans:ital,wght@0,300;0,400;0,600;1,300;1,400&display=swap" rel="stylesheet">
<style>
:root{
  --ink:#2b2b2b;
  --muted:#6a6a6a;
  --line:#c9c9c9;
  --panel:#fafafa;
  --teal:#27c1d4;
  --red:#d8171c;
  --white:#ffffff;
}
*{box-sizing:border-box;margin:0;padding:0}
html,body{width:918px;height:1200px;overflow:hidden;background:var(--white)}
body{font-family:"Nunito Sans",Arial,sans-serif;color:var(--ink);position:relative}
.abs{position:absolute}

.topbar{left:56px;top:16px;font-size:8px;letter-spacing:.3px;color:var(--muted);display:flex;gap:7px}
.topbar .sep{color:#999}
.social{left:598px;top:12px;display:flex;gap:6px}
.social span{width:21px;height:21px;border-radius:2px;display:block}
.search{left:738px;top:12px;width:124px;height:20px;border:1px solid var(--line);font-size:8px;font-style:italic;color:#888;padding:5px 9px}
.search svg{position:absolute;right:5px;top:4px}

.header{left:56px;top:46px;width:806px;height:111px;border:1px solid var(--line);background:var(--panel)}
.brand{position:absolute;left:0;right:0;top:25px;text-align:center;font-size:24px;font-weight:300;color:var(--teal);letter-spacing:.5px}
.nav{position:absolute;left:0;right:0;top:72px;border-top:1px solid var(--line);height:38px;display:flex;align-items:center;padding-left:17px;font-size:9.5px}
.nav a{color:var(--ink);text-decoration:none;margin-right:36px}
.cart{position:absolute;right:11px;top:12px;font-size:9.5px;display:flex;align-items:center;gap:6px}
.cart b{color:var(--teal);font-weight:400}

.banner{left:56px;top:163px;width:806px;height:267px;border:1px solid #999;background:linear-gradient(90deg,#e8955a 0%,#f0a468 40%,#9a6a48 62%,#4a3a36 80%,#6e5a52 100%)}
.banner h1{position:absolute;left:20px;top:56px;font-size:24px;font-weight:400;line-height:31px;color:#222;width:380px}
.banner h1 em{font-style:normal;color:var(--red)}
.btn-shop{position:absolute;left:20px;top:167px;width:113px;height:34px;background:var(--teal);color:var(--white);font-size:13px;display:flex;align-items:center;justify-content:center}
.dots{position:absolute;left:20px;top:241px;display:flex;gap:6px}
.dots i{width:6px;height:6px;border-radius:50%;background:#333;display:block}
.dots i:first-child{background:var(--teal)}

.promo{top:446px;height:84px;border:1px solid var(--line);padding:3px}
.promo div{border:1px solid var(--line);height:100%;text-align:center;padding-top:17px}
.promo h2{font-size:17px;font-weight:400;color:var(--teal)}
.promo p{font-size:13px;margin-top:5px}

.section-title{left:56px;top:555px;font-size:17px;font-weight:400}

.product{top:591px;width:185px;height:274px;border:1px solid var(--line)}
.product .photo{height:171px}
.product .name{text-align:center;font-size:10.5px;line-height:14px;margin-top:10px}
.product .price{text-align:center;font-size:14px;color:var(--teal);margin-top:5px}
.product .actions{position:absolute;left:0;right:0;bottom:0;height:33px;border-top:1px solid var(--line);display:flex;justify-content:space-between;align-items:center;padding:0 13px;font-size:8.5px;color:var(--muted)}
.product .actions span{display:flex;align-items:center;gap:5px}

.testimonials{left:56px;top:885px;width:806px;height:142px;border:1px solid var(--line);padding:3px}
.testimonials .inner{border:1px solid var(--line);height:100%;position:relative}
.testimonials h3{position:absolute;left:13px;top:13px;font-size:14.5px;font-weight:400}
.quote{position:absolute;top:48px;width:240px}
.quote .avatar{position:absolute;left:0;top:5px;width:20px;height:40px}
.quote p{margin-left:52px;font-size:9px;font-style:italic;font-weight:300;line-height:15.5px;color:#444}
.quote .who{margin-left:52px;margin-top:9px;font-size:9px;font-style:italic;color:var(--teal);line-height:12px}
.quote .where{margin-left:52px;font-size:9px;font-style:italic;line-height:12px}

.newsletter{left:56px;top:1045px;width:806px;height:72px;border:1px solid var(--line)}
.newsletter h3{position:absolute;left:17px;top:26px;font-size:14px;font-weight:400}
.newsletter .field{position:absolute;left:189px;top:17px;width:412px;height:38px;border:1px solid var(--line);font-size:8.5px;font-style:italic;color:#888;padding:13px 20px}
.newsletter .subscribe{position:absolute;left:617px;top:17px;width:173px;height:38px;background:var(--teal);color:var(--white);font-size:11.5px;display:flex;align-items:center;justify-content:center}

.footer{left:56px;top:1133px;width:806px;height:46px;border:1px solid var(--line)}
.footer p{position:absolute;left:14px;top:17px;font-size:8px;color:var(--muted)}
.cards{position:absolute;right:15px;top:15px;display:flex;gap:4px}
.cards span{width:24px;height:15px;border:1px solid #ccc;border-radius:2px;display:block}
</style>
</head>
<body>

<nav class="abs topbar"><span>LOG IN</span><span class="sep">|</span><span>REGISTER</span><span class="sep">|</span><span>MY ACCOUNT</span><span class="sep">|</span><span>WISHLIST</span><span class="sep">|</span><span>FAQ</span></nav>

<div class="abs social" aria-label="Social links">
  <span style="background:#3b5b9a"></span><span style="background:#1da1f2"></span><span style="background:#3f6f95"></span><span style="background:#c8232c"></span><span style="background:#dd4b39"></span>
</div>
<div class="abs search">Search...
  <svg width="12" height="12" viewBox="0 0 12 12"><circle cx="5" cy="5" r="3.6" fill="none" stroke="#333" stroke-width="1.3"/><line x1="7.7" y1="7.7" x2="11" y2="11" stroke="#333" stroke-width="1.5"/></svg>
</div>

<header class="abs header">
  <div class="brand">Tresses by Jolavie</div>
  <nav class="nav">
    <a>HOME</a><a>ABOUT US</a><a>OUR PRODUCTS</a><a>SHOP</a><a>BLOG</a><a>SPECIALS</a><a>TESTIMONIALS</a><a>CONTACT</a>
    <div class="cart">
      <svg width="13" height="14" viewBox="0 0 13 14"><path d="M1 4h11l-1 10H2z" fill="#999"/><path d="M4 4V3a2.5 2.5 0 0 1 5 0v1" fill="none" stroke="#999"/></svg>
      <span><b>MY CART:</b> $0.00</span>
    </div>
  </nav>
</header>

<section class="abs banner" role="img" aria-label="Banner photo of a smiling woman with long wavy hair beside a child in a kitchen">
  <h1>We sell <em>100% Human Hair</em> in Brazilian body wave deep wave straight or natural curl.</h1>
  <div class="btn-shop">SHOP NOW ››</div>
  <div class="dots"><i></i><i></i><i></i></div>
</section>

<div class="abs promo" style="left:56px;width:393px"><div><h2>GET 25% OFF WHEN U SPEND $100</h2><p>Duis aliquam nibh a dui iaculis viverra id</p></div></div>
<div class="abs promo" style="left:470px;width:392px"><div><h2>FREE SHIPPINF ON ALL ORDERS</h2><p>Duis aliquam nibh a dui iaculis viverra id</p></div></div>

<h2 class="abs section-title">HAIR COLLECTIONS</h2>

<article class="abs product" style="left:56px">
  <div class="photo" role="img" aria-label="Customer photo wearing curly hair" style="background:linear-gradient(160deg,#d8d8d8,#3a2e2c 60%,#6b5a55)"></div>
  <div class="name">Vestibulum ante ipsum<br>primis neque</div><div class="price">$123.00</div>
  <div class="actions"><span>MORE INFO</span><span><svg width="10" height="11" viewBox="0 0 13 14"><path d="M1 4h11l-1 10H2z" fill="#999"/></svg>ADD TO CART</span></div>
</article>
<article class="abs product" style="left:263px">
  <div class="photo" role="img" aria-label="Customer photo wearing straight shoulder-length hair" style="background:linear-gradient(170deg,#6a4a38,#3a2622 50%,#d8545a)"></div>
  <div class="name">Vestibulum ante ipsum<br>primis neque</div><div class="price">$123.00</div>
  <div class="actions"><span>MORE INFO</span><span><svg width="10" height="11" viewBox="0 0 13 14"><path d="M1 4h11l-1 10H2z" fill="#999"/></svg>ADD TO CART</span></div>
</article>
<article class="abs product" style="left:470px">
  <div class="photo" role="img" aria-label="Customer photo wearing a sleek bob" style="background:linear-gradient(160deg,#c9d2dc,#33363e 50%,#5b7bb0)"></div>
  <div class="name">Vestibulum ante ipsum<br>primis neque</div><div class="price">$123.00</div>
  <div class="actions"><span>MORE INFO</span><span><svg width="10" height="11" viewBox="0 0 13 14"><path d="M1 4h11l-1 10H2z" fill="#999"/></svg>ADD TO CART</span></div>
</article>
<article class="abs product" style="left:677px">
  <div class="photo" role="img" aria-label="Customer photo showing long wavy hair from behind in a kitchen" style="background:linear-gradient(180deg,#b78a55,#2c3350 55%,#8a5a34)"></div>
  <div class="name">Vestibulum ante ipsum<br>primis neque</div><div class="price">$123.00</div>
  <div class="actions"><span>MORE INFO</span><span><svg width="10" height="11" viewBox="0 0 13 14"><path d="M1 4h11l-1 10H2z" fill="#999"/></svg>ADD TO CART</span></div>
</article>

<section class="abs testimonials"><div class="inner">
  <h3>TESTIMONIALS</h3>
  <div class="quote" style="left:13px">
    <div class="avatar" role="img" aria-label="Customer portrait" style="width:40px;background:linear-gradient(135deg,#b01828,#3a1a20)"></div>
    <p>“ Vestibulum vel metus sit amet turpis bibendumtincidunt vel sit amet quam. Pellentesque habitant morbi tristique...”</p>
    <div class="who">-Name goes here</div><div class="where">Location</div>
  </div>
  <div class="quote" style="left:284px">
    <div class="avatar" role="img" aria-label="Customer portrait" style="width:40px;background:linear-gradient(135deg,#5a4a48,#1e1a1a)"></div>
    <p>“ Vestibulum vel metus sit amet turpis bibendumtincidunt vel sit amet quam. Pellentesque habitant morbi tristique...”</p>
    <div class="who">-Name goes here</div><div class="where">Location</div>
  </div>
  <div class="quote" style="left:553px">
    <div class="avatar" role="img" aria-label="Customer portrait" style="width:40px;background:linear-gradient(135deg,#7a8a6a,#3a2e2a)"></div>
    <p>“ Vestibulum vel metus sit amet turpis bibendumtincidunt vel sit amet quam. Pellentesque habitant morbi tristique...”</p>
    <div class="who">-Name goes here</div><div class="where">Location</div>
  </div>
</div></section>

<section class="abs newsletter">
  <h3>NEWSLETTER SIGN UP</h3>
  <div class="field">Enter email address...</div>
  <div class="subscribe">SUBSCRIBE NOW</div>
</section>

<footer class="abs footer">
  <p>Copyright © 2014. Company Name. All Right Reserved &nbsp;|&nbsp; Privacy Policy</p>
  <div class="cards" aria-label="Accepted payment methods">
    <span style="background:#fff"></span><span style="background:#1e3a6e"></span><span style="background:#f2f2f2"></span><span style="background:#2f6fb5"></span><span style="background:#fff"></span><span style="background:#2a4f8a"></span><span style="background:#111"></span><span style="background:#1e3a6e"></span><span style="background:#111"></span><span style="background:#5a3a7a"></span><span style="background:#1e4a3a"></span>
  </div>
</footer>

</body>
</html>
```